App Design - Career Prep Pal

We require an App Design for our new App called 'Hiring Helper'. This app is essentially an assistant to help Users prepare for job interviews, to help them get hired. <br/><br/>Users who download the App can view common Questions and Answers, save their favourite responses and also view common Interview Tips. <br/><br/>The vision for our App is for Users who are preparing for an interview (1 week before, 1 day before, even 1 hour before), are able to download, view and educate themselves on common questions and responses, and then be confident to land the job. <br/><br/>Our team has developed wireframes to help highlight what each screen should do and include. Please see attached document, which also highlights key requirements for the experience. Feel free to add/remove/edit what you see on these wireframes. Our preference is that you use Adobe XD please.<br/><br/>In terms of design guidelines, we want the experience to be simple, intuitive and 'memorable' to help Users to remember the questions/responses when they are in the interview. <br/><br/>The final design should communicate 'neat and clean professionalism'; we like the design of: jobvista net au<br/><br/>Thank you for reading! Good luck !

Target Market(s)

Professional job seekers

Font styles to use
Sans Serif

Colors

Designer to choose colors to be used in the design.

Requirements
Must have
• Please see my PixelGuild_UX file that I have uploaded
Nice to have
• Could you also please include some ideas on how we can incorporate Advertising into the app screens

```html
<!DOCTYPE html>
<html lang="en">
<head>
<meta charset="utf-8">
<title>Hiring Helper – Question Categories</title>
<link rel="stylesheet" href="https://fonts.googleapis.com/css2?family=Montserrat:wght@800&family=Nunito+Sans:wght@400;600&display=swap">
<style>
  :root {
    --brand-blue: #1658e0;
    --brand-blue-deep: #0f47c4;
    --button-blue: #1249b5;
    --page-bg: #f3f3f3;
    --card-bg: #ffffff;
    --ink: #000000;
    --white: #ffffff;
  }
  * { margin: 0; padding: 0; box-sizing: border-box; }
  html, body { width: 1200px; height: 2598px; overflow: hidden; }
  body {
    position: relative;
    background: var(--page-bg);
    font-family: "Nunito Sans", Arial, sans-serif;
    color: var(--ink);
  }
  .header {
    position: absolute; left: 0; top: 0; width: 1200px; height: 425px;
    background: linear-gradient(135deg, var(--brand-blue) 0%, #1a5ce6 45%, var(--brand-blue-deep) 100%);
  }
  .status-bar {
    position: absolute; left: 0; top: 0; width: 1200px; height: 110px;
    color: var(--white);
  }
  .status-time {
    position: absolute; left: 40px; top: 34px;
    font-family: "Nunito Sans", Arial, sans-serif; font-weight: 600; font-size: 40px;
  }
  .status-icons { position: absolute; right: 40px; top: 42px; }
  .back-button { position: absolute; left: 40px; top: 217px; }
  .screen-title {
    position: absolute; left: 141px; top: 203px;
    font-family: "Montserrat", Arial, sans-serif; font-weight: 800;
    font-size: 59px; letter-spacing: -0.5px; line-height: 70px;
    color: var(--white); white-space: nowrap;
  }
  .section-heading {
    position: absolute; left: 0; top: 505px; width: 1200px; text-align: center;
    font-family: "Montserrat", Arial, sans-serif; font-weight: 800;
    font-size: 50px; letter-spacing: -1.2px; line-height: 60px;
  }
  .category-card {
    position: absolute; left: 48px; width: 1109px; height: 333px;
    background: var(--card-bg); border-radius: 20px;
    box-shadow: 0 4px 22px rgba(0,0,0,0.06);
    display: flex; align-items: center; justify-content: center;
    font-size: 55px; font-weight: 400; letter-spacing: 0.3px;
  }
  .card-behavioural { top: 659px; }
  .card-situational { top: 1068px; }
  .card-motivational { top: 1485px; }
  .card-technical { top: 1881px; }
  .view-all-button {
    position: absolute; left: 48px; top: 2280px; width: 1109px; height: 226px;
    background: var(--button-blue); border-radius: 20px;
    display: flex; align-items: center; justify-content: center;
    font-family: "Montserrat", Arial, sans-serif; font-weight: 800;
    font-size: 54px; letter-spacing: -1px; color: var(--white);
  }
</style>
</head>
<body>
  <div class="header" role="img" aria-label="Blue-tinted photo of a person writing with a pen at an interview desk"></div>

  <div class="status-bar">
    <span class="status-time">9:41</span>
    <svg class="status-icons" width="120" height="30" viewBox="0 0 120 30" aria-hidden="true">
      <g fill="#ffffff">
        <rect x="0" y="19" width="6" height="9" rx="1"/>
        <rect x="10" y="14" width="6" height="14" rx="1"/>
        <rect x="20" y="9" width="6" height="19" rx="1"/>
        <rect x="30" y="3" width="6" height="25" rx="1"/>
      </g>
      <g fill="none" stroke="#ffffff" stroke-width="4" stroke-linecap="round">
        <path d="M50 12 a20 20 0 0 1 28 0"/>
        <path d="M55 18 a12 12 0 0 1 18 0"/>
      </g>
      <circle cx="64" cy="25" r="3.5" fill="#ffffff"/>
      <rect x="84" y="3" width="32" height="24" rx="6" fill="none" stroke="#ffffff" stroke-width="2.5"/>
      <rect x="88" y="7" width="24" height="16" rx="3" fill="#ffffff"/>
      <rect x="117.5" y="11" width="2.5" height="8" rx="1" fill="#ffffff"/>
    </svg>
  </div>

  <svg class="back-button" width="44" height="42" viewBox="0 0 44 42" aria-label="Back">
    <path d="M42 21 H5 M21 4 L4 21 L21 38" fill="none" stroke="#ffffff" stroke-width="5" stroke-linecap="round" stroke-linejoin="round"/>
  </svg>
  <h1 class="screen-title">VIEW QUESTION &amp; RESPONSES</h1>

  <h2 class="section-heading">SELECT YOUR QUESTION CATEGORY</h2>

  <div class="category-card card-behavioural">Behavioural</div>
  <div class="category-card card-situational">Situational</div>
  <div class="category-card card-motivational">Motivational</div>
  <div class="category-card card-technical">Technical</div>

  <div class="view-all-button">VIEW ALL</div>
</body>
</html>
```